Varnik Holdings — Business Card Design Brief
Overview
Design a double-sided business card for Varnik Holdings that highlights our two service arms: Varnik Communications (telecommunications) and Varnik Energy (business energy solutions). The card should feel smart and stand out when handed to clients.

Objectives
Showcase our areas of specialty clearly.
Reflect the overall Varnik / Varnik Holdings brand while acknowledging both arms.
Explore using both logos (Communications + Energy) or one unified logo, depending on the design.

Deliverables
One double-sided business card design (front + back).

Content & Copy
Front (preferred): Logo: Varnik / Varnik Holdings
Descriptor: Business Communications | Business Energy
Back:My contact details and company details
Core products: Business Mobile • Telephony • Internet • Business Energy Solutions

Brand & Visual Direction
We have a group logo currently tailored more toward telecoms, plus a separate Varnik Energy logo.
Please explore layouts that use both logos or just one, whichever works best.
Color: I wouldn't mind seeing an option using our the Blue/Purple gradient from our website (varnik-example.co.uk), but also open to non-gradient approaches and other colours..

Overall look: Smart, modern, and distinctive.
Format & Print Specs
Double-sided business card format. (Use a standard size

Must-Haves
Front: Varnik wording or Varnik Holdings wording with atleast 1 logo also on front “Business Communications | Business Energy.”

Back: Contact + company details and core products.
A design that stands out while remaining professional.

Nice-to-Have Options
A gradient version using our site’s Blue/Purple gradient.
A non-gradient version.
A dual-logo treatment versus a single-logo treatment.

Thanks
Owen

```html
<!DOCTYPE html>
<html lang="en">
<head>
<meta charset="utf-8">
<title>Varnik Holdings — Business Card</title>
<link rel="stylesheet" href="https://fonts.googleapis.com/css2?family=Arimo:wght@400;700&display=swap">
<style>
  :root {
    --backdrop: #dcdcdc;
    --navy: #1c1464;
    --green: #2da52b;
    --white: #ffffff;
    --comms-blue: #1e88e5;
    --energy-green: #7cb518;
    --rule: #8a8a8a;
  }
  html, body {
    margin: 0;
    padding: 0;
    width: 1200px;
    height: 1200px;
    overflow: hidden;
    background: var(--backdrop);
    font-family: "Arimo", Arial, sans-serif;
  }
  .canvas { position: relative; width: 1200px; height: 1200px; }
  .card {
    position: absolute;
    left: 255px;
    width: 690px;
    height: 394px;
    box-sizing: border-box;
  }
  .card--contact { top: 160px; background: var(--navy); color: var(--white); }
  .card--brand { top: 652px; background: var(--white); }

  /* contact side */
  .identity {
    position: absolute;
    right: 330px;
    top: 152px;
    text-align: right;
    font-size: 16.5px;
    line-height: 21px;
  }
  .identity__name {
    color: var(--green);
    font-weight: 700;
    font-size: 28px;
    line-height: 30px;
    margin-bottom: 3px;
    letter-spacing: 0.2px;
  }
  .contact-rule {
    position: absolute;
    left: 375px;
    top: 154px;
    width: 1px;
    height: 84px;
    background: rgba(255,255,255,0.75);
  }
  .contact-list {
    position: absolute;
    left: 392px;
    top: 155px;
    margin: 0;
    padding: 0;
    list-style: none;
    font-size: 16.5px;
    line-height: 20.5px;
  }
  .contact-list li { display: flex; align-items: center; gap: 9px; }
  .contact-list svg { width: 13px; height: 13px; fill: var(--green); flex: none; }
  .products {
    position: absolute;
    left: 0;
    right: 0;
    top: 326px;
    text-align: center;
    font-size: 17px;
    letter-spacing: 0.1px;
  }

  /* brand side */
  .brand-rule {
    position: absolute;
    left: 359px;
    top: 98px;
    width: 1px;
    height: 200px;
    background: var(--rule);
  }
  .arm {
    position: absolute;
    top: 178px;
    width: 300px;
    text-align: center;
  }
  .arm--comms { left: 66px; }
  .arm--energy { left: 372px; }
  .arm__name {
    display: inline-flex;
    align-items: center;
    gap: 10px;
    color: var(--navy);
    font-weight: 700;
    font-size: 50px;
    line-height: 52px;
  }
  .arm__dot { width: 20px; height: 20px; border-radius: 50%; }
  .arm--comms .arm__dot { background: var(--comms-blue); }
  .arm--energy .arm__dot { background: var(--energy-green); }
  .arm__descriptor { margin-top: 8px; font-size: 16px; }
  .arm--comms .arm__descriptor { color: var(--comms-blue); }
  .arm--energy .arm__descriptor { color: var(--energy-green); letter-spacing: 3px; }
</style>
</head>
<body>
<main class="canvas">
  <section class="card card--contact" aria-label="Business card, contact side">
    <div class="identity">
      <div class="identity__name">DANIEL MERCER</div>
      <div>President</div>
      <div>412 Larchwood Road</div>
      <div>Fernbridge, Canada 20418</div>
    </div>
    <div class="contact-rule"></div>
    <ul class="contact-list">
      <li><svg viewBox="0 0 24 24" aria-hidden="true"><path d="M6.6 10.8a15 15 0 0 0 6.6 6.6l2.2-2.2c.3-.3.7-.4 1-.2 1.1.4 2.3.6 3.6.6.6 0 1 .4 1 1V20c0 .6-.4 1-1 1A17 17 0 0 1 3 4c0-.6.4-1 1-1h3.5c.6 0 1 .4 1 1 0 1.3.2 2.5.6 3.6.1.3 0 .7-.2 1z"/></svg>555-201-4830</li>
      <li><svg viewBox="0 0 24 24" aria-hidden="true"><path d="M7 1h10a2 2 0 0 1 2 2v18a2 2 0 0 1-2 2H7a2 2 0 0 1-2-2V3a2 2 0 0 1 2-2zm0 3v15h10V4zm4 16.5a1 1 0 1 0 2 0 1 1 0 0 0-2 0z"/></svg>555-201-7719</li>
      <li><svg viewBox="0 0 24 24" aria-hidden="true"><path d="M2 5h20v14H2zm2 2v.5l8 5 8-5V7zm0 3v7h16v-7l-8 5z"/></svg>info@varnik-example.co.uk</li>
      <li><svg viewBox="0 0 24 24" aria-hidden="true"><path d="M12 2a10 10 0 1 0 0 20 10 10 0 0 0 0-20zm-1 17.9A8 8 0 0 1 4.2 10.2L9 15v1a2 2 0 0 0 2 2zm6.9-2.5A2 2 0 0 0 16 16h-1v-3a1 1 0 0 0-1-1H8v-2h2a1 1 0 0 0 1-1V7h2a2 2 0 0 0 2-2v-.4a8 8 0 0 1 2.9 12.8z"/></svg>www.varnik-example.co.uk</li>
    </ul>
    <p class="products" style="margin:0">Business Mobile &nbsp;•&nbsp; Telephony &nbsp;•&nbsp; Internet &nbsp;•&nbsp; Business Energy Solutions</p>
  </section>

  <section class="card card--brand" aria-label="Business card, brand side">
    <div class="arm arm--comms">
      <div class="arm__name"><span class="arm__dot"></span>VARNIK</div>
      <div class="arm__descriptor">BUSINESS COMMUNICATIONS</div>
    </div>
    <div class="brand-rule"></div>
    <div class="arm arm--energy">
      <div class="arm__name"><span class="arm__dot"></span>VARNIK</div>
      <div class="arm__descriptor">BUSINESS ENERGY</div>
    </div>
  </section>
</main>
</body>
</html>
```